The design should look similar to the uploaded example to accommodate the information needed for a business card template. I would like to see the colors orange and charcoal grey incorporated along with the logo.The following should be on the back of the card SPECIALIZING IN NEW AND USED TIRES & WHEELS FOR:- Loaders- Skid Steers- Telehandlers- Boom Lifts- Forklifs and moreELIMINATING DOWNTIMEWheel Exchange Program for New & Used Foam Filled and Solid Rubber TiresSPECIALTY SERVICES- Foam Filling Tires- Largest Tire Press in SE- ONSITE Forklift Tire Press- Boom Truck Services - Rubber Tracks

Target Market(s)

New and Existing Customers

Industry/Entity Type

Business

Contact Information for Business Card

NAMEHEAVY DUTY TIRE, LLC8470 Belvedere RoadWest Palm Beach, FL 33411P: 844-HD-TIRESF: 561-431-6469C:E: W: WWW.GRANITERIMSUPPLY-EXAMPLE.COM

Font styles to use
Sans Serif

Colors
f37122
333333

Requirements
Must have
• The logo and the information indicated for the backside of the card
Nice to have
• Keep the orange and charcoal grey colors

```html
<!DOCTYPE html>
<html lang="en">
<head>
<meta charset="utf-8">
<title>Granite Rim Supply, LLC — Business Card</title>
<link href="https://fonts.googleapis.com/css2?family=Open+Sans:wght@400;600;700;800&display=swap" rel="stylesheet">
<style>
  :root {
    --orange: #f37122;
    --charcoal: #333333;
    --slate: #37474a;
    --white: #ffffff;
    --backdrop: #2b2d31;
  }
  * { box-sizing: border-box; margin: 0; padding: 0; }
  html, body { width: 1200px; height: 864px; overflow: hidden; }
  body {
    background: var(--backdrop);
    font-family: "Open Sans", Arial, sans-serif;
    position: relative;
  }
  .card {
    position: absolute;
    width: 560px;
    height: 320px;
    overflow: hidden;
    box-shadow: 0 10px 24px rgba(0,0,0,0.45);
  }

  /* Back side */
  .card-back {
    left: 300px; top: 70px;
    background: var(--orange);
    color: var(--white);
  }
  .back-services {
    position: absolute; left: 40px; top: 46px; width: 220px;
    text-align: right;
  }
  .back-specialty {
    position: absolute; left: 296px; top: 46px; width: 240px;
  }
  .back-heading {
    font-weight: 700; font-size: 16px; line-height: 1.15;
    text-transform: uppercase; margin-bottom: 10px; text-align: center;
  }
  .back-list { list-style: none; font-size: 13.5px; font-weight: 600; line-height: 1.45; }
  .back-services .back-list li::after { content: " \2022"; margin-left: 4px; }
  .back-specialty .back-list li::before { content: "\2022 "; margin-right: 4px; }
  .back-downtime {
    position: absolute; left: 0; right: 0; top: 222px;
    text-align: center; font-size: 14px; font-weight: 600; line-height: 1.25;
  }
  .back-downtime strong { display: block; font-weight: 700; text-transform: uppercase; }

  /* Front side */
  .card-front {
    left: 240px; top: 470px;
    background: var(--white);
  }
  .front-top-band { position: absolute; left: 0; right: 0; top: 0; height: 34px; background: var(--orange); }
  .front-rule { position: absolute; left: 0; right: 0; top: 40px; height: 4px; background: var(--slate); }
  .front-title-band {
    position: absolute; left: 230px; right: 0; top: 50px; height: 46px;
    background: var(--orange);
    display: flex; align-items: center; justify-content: center;
  }
  .company-name {
    font-weight: 800; font-size: 21px; color: var(--slate);
    letter-spacing: 0.3px; white-space: nowrap;
  }
  .front-title-rule { position: absolute; left: 230px; right: 0; top: 99px; height: 3px; background: var(--slate); }
  .front-bottom-band {
    position: absolute; left: 0; right: 0; bottom: 0; height: 56px;
    background: var(--slate);
  }
  .website {
    position: absolute; left: 28px; bottom: 14px;
    color: var(--white); font-weight: 700; font-size: 19px;
  }
  .brand-mark {
    position: absolute; left: 18px; top: 52px; width: 210px; height: 200px;
    display: flex; flex-direction: column; align-items: center; justify-content: center;
    gap: 10px;
  }
  .brand-dot { width: 110px; height: 110px; border-radius: 50%; background: var(--orange); border: 10px solid var(--charcoal); }
  .brand-name {
    font-weight: 800; font-size: 22px; color: var(--charcoal);
    text-transform: uppercase;
  }
  .contact {
    position: absolute; right: 22px; top: 108px; width: 300px;
    text-align: right; color: var(--charcoal);
  }
  .person-name { color: var(--orange); font-weight: 700; font-size: 18px; line-height: 1.3; margin-bottom: 8px; margin-right: 10px; }
  .address { font-size: 13.5px; line-height: 1.25; margin-bottom: 6px; }
  .contact-list { list-style: none; font-size: 13.5px; line-height: 1.35; }
  .contact-list li { display: flex; justify-content: flex-end; align-items: center; gap: 8px; }
  .contact-list svg { width: 12px; height: 12px; fill: var(--orange); flex: none; }
</style>
</head>
<body>

<section class="card card-back" aria-label="Business card back">
  <div class="back-services">
    <h2 class="back-heading">Specialty Services</h2>
    <ul class="back-list">
      <li>Foam Filling Tires</li>
      <li>Largest Tire Press in SE</li>
      <li>ONSITE Forklift Tire Press</li>
      <li>Boom Truck Services</li>
      <li>Rubber Tracks</li>
    </ul>
  </div>
  <div class="back-specialty">
    <h2 class="back-heading">Specializing in new and used tires &amp; wheels for:</h2>
    <ul class="back-list">
      <li>Loaders</li>
      <li>Skid Steers</li>
      <li>TelehandlersBoom Lifts</li>
      <li>Forklifs and more</li>
    </ul>
  </div>
  <p class="back-downtime">
    <strong>Eliminating Downtime</strong>
    Wheel Exchange Program for New &amp; Used Foam<br>Filled and Solid Rubber Tires
  </p>
</section>

<section class="card card-front" aria-label="Business card front">
  <div class="front-top-band"></div>
  <div class="front-rule"></div>
  <div class="front-title-band"><h1 class="company-name">GRANITE RIM SUPPLY, LLC</h1></div>
  <div class="front-title-rule"></div>
  <div class="front-bottom-band"></div>

  <div class="brand-mark">
    <span class="brand-dot" aria-hidden="true"></span>
    <span class="brand-name">Granite Rim</span>
  </div>

  <div class="contact">
    <p class="person-name">Daniel Mercer</p>
    <p class="address">5126 Marston Lane<br>West Palm Beach, FL 33411</p>
    <ul class="contact-list">
      <li>844-GR-WHEEL
        <svg viewBox="0 0 24 24" aria-hidden="true"><path d="M6.6 10.8a15 15 0 0 0 6.6 6.6l2.2-2.2a1 1 0 0 1 1-.25 11.4 11.4 0 0 0 3.6.57 1 1 0 0 1 1 1V20a1 1 0 0 1-1 1A17 17 0 0 1 3 4a1 1 0 0 1 1-1h3.5a1 1 0 0 1 1 1c0 1.25.2 2.45.57 3.57a1 1 0 0 1-.25 1z"/></svg></li>
      <li>561-278-9053
        <svg viewBox="0 0 24 24" aria-hidden="true"><path d="M6 2h9v6H6zM4 9h16a2 2 0 0 1 2 2v8H2v-8a2 2 0 0 1 2-2zm3 4v2h2v-2zm4 0v2h2v-2zm4 0v2h2v-2z"/></svg></li>
      <li>561-390-7714
        <svg viewBox="0 0 24 24" aria-hidden="true"><path d="M7 1h10a2 2 0 0 1 2 2v18a2 2 0 0 1-2 2H7a2 2 0 0 1-2-2V3a2 2 0 0 1 2-2zm0 3v14h10V4zm5 15.5a1 1 0 1 0 0 2 1 1 0 0 0 0-2z"/></svg></li>
      <li>info@graniterim-example.com
        <svg viewBox="0 0 24 24" aria-hidden="true"><path d="M2 5h20v14H2zm2 2v.5l8 5 8-5V7zm0 2.8V17h16V9.8l-8 5z"/></svg></li>
    </ul>
  </div>

  <p class="website">www.graniterimsupply-example.com</p>
</section>

</body>
</html>
```